Promotional brochure for educational consulting firm

Updates

Hi Designers!

Please do a 8.5 x 11 inch tri-fold brochure as well as a 8.5 x 11 inch half-fold brochure.  I appreciate black and white versions in addition to color.  Please take a look at my company's website for a better sense of the look and feel I am going for:  www.brightlanepa.org

Thanks!

Industry/Entity Type

Consulting

Colors
3176b5
85abd2
fcfbfd

```html
<!DOCTYPE html>
<html lang="en">
<head>
<meta charset="utf-8">
<title>Brightlane Associates – Tri-fold Brochure</title>
<link href="https://fonts.googleapis.com/css2?family=Nunito:wght@400;600;700;900&display=swap" rel="stylesheet">
<style>
  :root {
    --brand-blue: #3176b5;
    --brand-blue-deep: #1d5ca8;
    --brand-blue-soft: #85abd2;
    --paper: #fcfbfd;
    --paper-shade: #eeeef0;
    --ink: #1e1e1e;
    --ink-soft: #3a3a3a;
    --fold-line: #cfcfd3;
    --backdrop: #e6e6e8;
  }
  * { box-sizing: border-box; margin: 0; padding: 0; }
  html, body { width: 1200px; height: 945px; overflow: hidden; }
  body {
    background: var(--backdrop);
    font-family: "Nunito", Arial, sans-serif;
    color: var(--ink);
  }
  .brochure {
    position: absolute;
    left: 38px; top: 38px;
    width: 1124px; height: 856px;
    display: grid;
    grid-template-columns: repeat(3, 1fr);
    grid-template-rows: 252px 40px 284px 40px 240px;
    background: var(--paper);
    box-shadow: 0 10px 0 -2px #2a2a2a, 0 6px 18px rgba(0,0,0,.25);
  }
  .panel-top, .panel-bottom {
    background: linear-gradient(180deg, var(--paper) 0%, var(--paper-shade) 100%);
    display: flex; flex-direction: column; align-items: center; justify-content: center;
    text-align: center;
    position: relative;
  }
  .band { background: var(--brand-blue); }
  .fold { border-right: 1px solid var(--fold-line); }
  .photo { width: 100%; height: 100%; }
  .photo--pencils {
    background: linear-gradient(160deg, #1b1b1b 0%, #8a4a2a 20%, #d23a3a 38%, #e6c23a 52%, #2f56b8 66%, #d34d93 80%, #4a3aa0 100%);
  }
  .photo--cheering {
    background: radial-gradient(ellipse at 50% 75%, #f4d34a 0%, #e46a3a 25%, #7cc3e4 48%, #ffffff 80%);
  }
  .photo--reading {
    background: radial-gradient(ellipse at 50% 60%, #f0c23a 0%, #6fa6d8 35%, #e8c7a8 55%, #ffffff 85%);
  }

  .contact { justify-content: flex-start; padding-top: 30px; }
  .contact__label { color: var(--brand-blue-soft); font-weight: 700; font-size: 16px; letter-spacing: .5px; }
  .contact__name { color: var(--brand-blue-deep); font-size: 19px; margin-top: 20px; }
  .contact__line { display: flex; align-items: center; gap: 5px; font-size: 14px; color: var(--ink-soft); }
  .contact__line svg { width: 14px; height: 14px; }
  .contact__line--phone { font-weight: 700; font-size: 16px; color: var(--ink); margin-top: 22px; }
  .contact__line--fax { margin-top: 14px; }
  .contact__line--email { margin-top: 18px; }
  .contact__line--web { margin-top: 12px; }

  .headline__lead { font-size: 29px; color: var(--ink); margin-top: 8px; }
  .headline__figure { font-size: 62px; font-weight: 900; color: var(--brand-blue-deep); line-height: 1.1; letter-spacing: 1px; }

  .brand { display: flex; flex-direction: column; align-items: center; }
  .brand__row { display: flex; align-items: center; gap: 10px; }
  .brand__dot { width: 22px; height: 22px; border-radius: 50%; background: var(--brand-blue-deep); }
  .brand__name { font-size: 22px; font-weight: 700; color: var(--brand-blue-deep); }
  .brand__tagline { font-size: 12.5px; color: var(--brand-blue-deep); text-transform: uppercase; letter-spacing: .3px; margin-top: 4px; }

  .callout { justify-content: flex-end; padding-bottom: 44px; }
  .callout__mark {
    position: absolute; left: 50%; top: 22px; transform: translateX(-50%);
    width: 200px; height: 200px; border-radius: 50%; border: 26px solid #e9e9ec;
  }
  .callout__phone { position: relative; display: flex; align-items: center; gap: 6px; font-size: 22px; font-weight: 700; }
  .callout__phone svg { width: 22px; height: 22px; }
  .callout__web { position: relative; display: flex; align-items: center; gap: 5px; font-size: 15px; color: var(--ink-soft); margin-top: 6px; }
  .callout__web svg { width: 13px; height: 13px; }

  .closing { font-size: 27px; line-height: 1.25; color: var(--brand-blue-deep); }
</style>
</head>
<body>
<main class="brochure">
  <!-- top row -->
  <section class="panel-top contact fold">
    <p class="contact__label">CONTACT US</p>
    <p class="contact__name">Dana Whitfield, Ed.D.</p>
    <p class="contact__line contact__line--phone">
      <svg viewBox="0 0 16 16"><circle cx="8" cy="8" r="7" fill="none" stroke="#1e1e1e" stroke-width="1.2"/><path d="M6 4c-1 1-1 3 1 5s4 2 5 1l-1.5-1.5-1 .6c-.8-.4-1.8-1.4-2.2-2.2l.6-1z" fill="#1e1e1e"/></svg>
      555.014.2290</p>
    <p class="contact__line contact__line--fax">
      <svg viewBox="0 0 16 16"><rect x="2" y="8" width="12" height="6" fill="none" stroke="#3176b5" stroke-width="1.2"/><path d="M5 8V2h6v6" fill="none" stroke="#3176b5" stroke-width="1.2"/></svg>
      555.014.7736</p>
    <p class="contact__line contact__line--email">
      <svg viewBox="0 0 16 16"><rect x="1" y="3" width="14" height="10" fill="#3176b5"/><path d="M1 3l7 6 7-6" fill="none" stroke="#fff" stroke-width="1.2"/></svg>
      dana@brightlanepa.org</p>
    <p class="contact__line contact__line--web">
      <svg viewBox="0 0 16 16"><circle cx="8" cy="8" r="7" fill="#3176b5"/><path d="M1 8h14M8 1v14M3 4.5h10M3 11.5h10" stroke="#fff" stroke-width=".9"/></svg>
      www.brightlanepa.org</p>
  </section>
  <section class="panel-top headline fold">
    <p class="headline__lead">School leadership is</p>
    <p class="headline__figure">24/7/365</p>
  </section>
  <section class="panel-top brand">
    <div class="brand__row"><span class="brand__dot"></span><span class="brand__name">Brightlane Associates LLC</span></div>
    <p class="brand__tagline">Supporting schools &amp; school leaders</p>
  </section>

  <div class="band fold"></div><div class="band fold"></div><div class="band"></div>

  <div class="photo photo--pencils" role="img" aria-label="Close-up of sharpened coloured pencils"></div>
  <div class="photo photo--cheering" role="img" aria-label="Group of cheerful schoolchildren with backpacks raising their arms"></div>
  <div class="photo photo--reading" role="img" aria-label="Three smiling children lying on the floor with an open book"></div>

  <div class="band fold"></div><div class="band fold"></div><div class="band"></div>

  <!-- bottom row -->
  <section class="panel-bottom brand fold" style="justify-content:flex-end;padding-bottom:30px;">
    <div class="brand__row"><span class="brand__dot"></span><span class="brand__name">Brightlane Associates LLC</span></div>
    <p class="brand__tagline">Supporting schools &amp; school leaders</p>
  </section>
  <section class="panel-bottom callout fold">
    <span class="callout__mark" aria-hidden="true"></span>
    <p class="callout__phone">
      <svg viewBox="0 0 16 16"><circle cx="8" cy="8" r="7" fill="none" stroke="#1e1e1e" stroke-width="1.2"/><path d="M6 4c-1 1-1 3 1 5s4 2 5 1l-1.5-1.5-1 .6c-.8-.4-1.8-1.4-2.2-2.2l.6-1z" fill="#1e1e1e"/></svg>
      555.014.2290</p>
    <p class="callout__web">
      <svg viewBox="0 0 16 16"><circle cx="8" cy="8" r="7" fill="#3176b5"/><path d="M1 8h14M8 1v14M3 4.5h10M3 11.5h10" stroke="#fff" stroke-width=".9"/></svg>
      www.brightlanepa.org</p>
  </section>
  <section class="panel-bottom">
    <p class="closing">Let’s work together<br>to take your school<br>to the next<br>level of excellence.</p>
  </section>
</main>
</body>
</html>
```